Business card for law firm

Need business card for new law firm. Think confident, authoritative, conservative, but not stuffy or old-fashioned.

Contact Information for Business Card

Content for card - logo (uploaded), plus the following:

Paul Whitcombe (larger font)
Managing Partner (larger font, but not as large as name)
Level 9, 7 Ferris Lane
Sydney NSW 2000
Main Tel 02 9364 2710
Direct Tel 02 8472 3159
Email paul@qvlegal.com.au
www.qvlegal.com.au

Letterhead design should include logo plus:
Level 9, 7 Ferris Lane
Sydney NSW 2000
Tel 02 8472 3159
www.qvlegal.com.au

```html
<!DOCTYPE html>
<html lang="en">
<head>
<meta charset="utf-8">
<title>Quayvale Legal – Business Card</title>
<link rel="stylesheet" href="https://fonts.googleapis.com/css2?family=Open+Sans:ital,wght@0,400;0,600;0,700;1,700&display=swap">
<style>
  :root {
    --navy: #0c1f5c;
    --ink: #1b1b1b;
    --grey: #4a4a4a;
    --paper: #ffffff;
    --backdrop: #2b2b2d;
  }
  * { margin: 0; padding: 0; box-sizing: border-box; }
  html, body { width: 1200px; height: 960px; overflow: hidden; }
  body {
    background: var(--backdrop);
    font-family: "Open Sans", Arial, sans-serif;
    position: relative;
  }
  .card {
    position: absolute;
    left: 250px;
    width: 700px;
    height: 400px;
    overflow: hidden;
  }
  /* Back of card */
  .card--back { top: 50px; background: var(--navy); }
  .back-brand {
    position: absolute;
    left: 0; right: 0; top: 160px;
    display: flex; align-items: center; justify-content: center; gap: 18px;
  }
  .brand-square { display: block; background: currentColor; }
  .back-brand .brand-square { width: 44px; height: 44px; color: var(--paper); }
  .back-brand .brand-name {
    color: var(--paper); font-weight: 600; font-size: 34px; letter-spacing: 4px;
  }
  .back-web {
    position: absolute; left: 0; right: 0; top: 318px; text-align: center;
    color: var(--paper); font-size: 15px; letter-spacing: 4px;
  }
  /* Front of card */
  .card--front { top: 510px; background: var(--paper); }
  .front-graphics { position: absolute; inset: 0; }
  .holder { position: absolute; left: 34px; top: 70px; }
  .holder-name {
    color: var(--navy); font-weight: 700; font-style: italic;
    font-size: 22px; text-transform: uppercase; letter-spacing: .3px;
  }
  .holder-title {
    color: var(--grey); font-size: 13.5px; text-transform: uppercase; margin-top: 1px;
  }
  .contacts { position: absolute; left: 34px; top: 158px; list-style: none; }
  .contacts li {
    display: flex; align-items: center; gap: 7px;
    color: var(--ink); font-size: 14px; line-height: 21px;
  }
  .contacts svg { width: 12px; height: 12px; flex: none; }
  .front-brand {
    position: absolute; right: 36px; top: 98px;
    display: flex; align-items: center; gap: 12px;
  }
  .front-brand .brand-square { width: 30px; height: 30px; color: var(--navy); }
  .front-brand .brand-name {
    color: var(--ink); font-weight: 600; font-size: 26px; letter-spacing: 3px;
  }
  .address {
    position: absolute; right: 36px; top: 272px; text-align: right;
    color: var(--ink); font-size: 15px; line-height: 21px;
  }
  .front-web {
    position: absolute; left: 330px; right: 0; top: 356px; text-align: center;
    color: var(--paper); font-size: 15px; letter-spacing: 3px;
  }
</style>
</head>
<body>

<section class="card card--back" aria-label="Card back">
  <div class="back-brand">
    <span class="brand-square"></span>
    <span class="brand-name">QUAYVALE LEGAL</span>
  </div>
  <p class="back-web">www.qvlegal.com.au</p>
</section>

<section class="card card--front" aria-label="Card front">
  <svg class="front-graphics" viewBox="0 0 700 400" width="700" height="400" aria-hidden="true">
    <line x1="214" y1="150" x2="700" y2="150" stroke="#1b1b1b" stroke-width="1.6"/>
    <polyline points="0,220 268,220 306,326" fill="none" stroke="#1b1b1b" stroke-width="5"/>
    <polygon points="0,230 264,230 302,336 700,336 700,400 305,400 252,242 0,242" fill="#0c1f5c"/>
  </svg>

  <div class="holder">
    <h1 class="holder-name">Paul Whitcombe</h1>
    <p class="holder-title">Managing Partner</p>
  </div>

  <ul class="contacts">
    <li>
      <svg viewBox="0 0 12 12"><circle cx="6" cy="6" r="6" fill="#0c1f5c"/><path d="M3.6 3.2l1.2-.4.7 1.5-.7.6c.3.8.9 1.4 1.7 1.7l.6-.7 1.5.7-.4 1.2c-2.4-.1-4.5-2.2-4.6-4.6z" fill="#fff"/></svg>
      02 9364 2710(Main)
    </li>
    <li>
      <svg viewBox="0 0 12 12"><circle cx="6" cy="6" r="6" fill="#0c1f5c"/><path d="M3.6 3.2l1.2-.4.7 1.5-.7.6c.3.8.9 1.4 1.7 1.7l.6-.7 1.5.7-.4 1.2c-2.4-.1-4.5-2.2-4.6-4.6z" fill="#fff"/></svg>
      02 8472 3159(Direct)
    </li>
    <li>
      <svg viewBox="0 0 12 12"><circle cx="6" cy="6" r="6" fill="#0c1f5c"/><rect x="3" y="4" width="6" height="4.2" fill="#fff"/><path d="M3 4l3 2.3L9 4" fill="none" stroke="#0c1f5c" stroke-width=".8"/></svg>
      paul@qvlegal.com.au
    </li>
  </ul>

  <div class="front-brand">
    <span class="brand-square"></span>
    <span class="brand-name">QUAYVALE LEGAL</span>
  </div>

  <address class="address" style="font-style:normal">
    Level 9, 7 Ferris Lane<br>
    Sydney NSW 2000
  </address>

  <p class="front-web">www.qvlegal.com.au</p>
</section>

</body>
</html>
```